Design Direct mailer post card for Carpet Cleaning business

We are looking to create a 6.5x 12 eyes cashing direct mail postcard (eddm) for mailed to residential .
This campaign is targeted towards residential customers, with the goal of introducing our service, promote our business, and gain some brand recognition.
The call-to-action is for the prospect to contact us and also schedule a free no obligation demonstration (call, visit our website, or send us an email) to find out information about our service, and to learn more about our service.
4 offers
One Free Room of carpet cleaning
Free bottle spot cleaner
Free Carpet audit
Free chair Cleaning
(See attached picture for offers)
Slogans-You will love your Carpet Again
You want believe the difference
No more Wet Carpet
Dries in minutes not hours
100% natural Safe for Kids and Pets
No harsh chemicals
No sticky residue
Improve air Quailty
100% guaranteed
As far as design, we are looking for a clean and simple layout, not too cluttered, but powerful enough to grab the attention of the reader. Less is more in this case. On the front we were thinking the use of an image & headline and on the back the rest of the information. With that said, please feel free to use your expertise and judgement to conceptualize the best design.
Also attach picture of design and color that I would like.
Target Market(s)
35-70 women middle to upper class
Industry/Entity Type
Cleaning Service

```html
<!DOCTYPE html>
<html lang="en">
<head>
<meta charset="utf-8">
<title>PureNest Carpet Cleaning Postcard</title>
<link rel="stylesheet" href="https://fonts.googleapis.com/css2?family=Lato:wght@400;700&family=Caveat:wght@500&family=Kalam:wght@400&display=swap">
<style>
  :root {
    --teal: #35b8a6;
    --teal-dark: #2b8f82;
    --teal-text: #3bb3a3;
    --green: #9ccb3b;
    --cream: #fdf5f0;
    --white: #ffffff;
    --script-green: #8cc63f;
    --photo-a: #c9c3c8;
    --photo-b: #8d8790;
  }
  * { margin: 0; padding: 0; box-sizing: border-box; }
  html, body { width: 1200px; height: 650px; overflow: hidden; background: var(--cream); }
  .postcard { position: relative; width: 1200px; height: 650px; background: var(--cream); font-family: "Lato", sans-serif; }

  .headline-band { position: absolute; left: 0; top: 0; width: 765px; height: 192px; background: var(--teal); }
  .headline { position: absolute; color: var(--white); font-weight: 700; font-size: 32px; white-space: nowrap; letter-spacing: 0.2px; }
  .headline--one { left: 44px; top: 54px; }
  .headline--two { left: 144px; top: 108px; }

  .services { position: absolute; left: 50px; top: 254px; }
  .services__title { color: var(--teal-text); font-weight: 700; font-size: 30px; margin-bottom: 24px; }
  .services__list { list-style: none; }
  .services__list li { color: var(--teal-text); font-size: 18px; line-height: 25px; padding-left: 12px; position: relative; }
  .services__list li::before { content: ""; position: absolute; left: 0; top: 10px; width: 5px; height: 8px; border-radius: 50% 50% 50% 0; background: var(--teal); opacity: .6; }

  .photo { position: absolute; left: 387px; top: 192px; width: 378px; height: 310px; background: linear-gradient(180deg, var(--photo-a) 0%, #b8b2b6 55%, var(--photo-b) 100%); }

  .divider { position: absolute; left: 0; top: 502px; width: 765px; height: 7px; background: var(--teal); }

  .brand { position: absolute; left: 48px; top: 556px; display: flex; align-items: center; gap: 10px; }
  .brand__mark { width: 14px; height: 14px; border-radius: 50%; background: var(--teal); }
  .brand__name { font-family: "Lato", sans-serif; font-weight: 400; font-size: 50px; color: var(--teal); line-height: 1; }

  .contact { position: absolute; left: 430px; top: 540px; width: 300px; text-align: center; }
  .contact__cta { font-family: "Kalam", cursive; font-size: 17px; color: var(--script-green); }
  .contact__phone { display: inline-flex; align-items: center; gap: 6px; font-weight: 700; font-size: 22px; color: var(--teal); margin-top: 2px; }
  .contact__web { font-size: 18px; color: var(--teal); margin-top: 4px; }

  .green-panel { position: absolute; left: 765px; top: 0; width: 435px; height: 650px; background: var(--green); }
  .green-claim { position: absolute; left: 67px; top: 108px; white-space: nowrap; color: var(--teal-dark); font-weight: 700; font-size: 32px; }
  .green-claim__hand { font-family: "Caveat", cursive; font-weight: 500; font-size: 40px; color: var(--white); margin-left: 6px; }
  .green-claim__underline { position: absolute; left: 207px; top: 150px; }

  .benefits { position: absolute; left: 23px; top: 220px; list-style: none; }
  .benefits li { display: flex; align-items: center; gap: 6px; color: var(--teal-dark); font-size: 21px; line-height: 29px; white-space: nowrap; }

  .guarantee { position: absolute; left: 88px; top: 410px; }
</style>
</head>
<body>
<main class="postcard">
  <section class="headline-band">
    <h1 class="headline headline--one">YOU WILL LOVE YOUR CARPET AGAIN</h1>
    <p class="headline headline--two">YOU WANT BELIEVE THE DIFFERENCE</p>
  </section>

  <section class="services">
    <h2 class="services__title">OUR SERVICES</h2>
    <ul class="services__list">
      <li>Carpet Cleaning</li>
      <li>Tile Cleaning</li>
      <li>Upholstery Cleaning</li>
      <li>Rug Cleaning</li>
      <li>Odor Removal &amp; Air Duct Cleaning</li>
    </ul>
  </section>

  <div class="photo" role="img" aria-label="Photo of a toddler lying on a soft grey shag carpet with a teddy bear, holding a bottle and a pink flower"></div>

  <div class="divider"></div>

  <div class="brand">
    <span class="brand__mark"></span>
    <span class="brand__name">PureNest</span>
  </div>

  <div class="contact">
    <p class="contact__cta">Call Today !</p>
    <p class="contact__phone">
      <svg width="18" height="22" viewBox="0 0 18 22" aria-hidden="true"><path d="M4 1 L7 6 L5 8 C6 12 8 15 11 17 L13 15 L17 18 L15 21 C7 20 1 12 1 4 Z" fill="#35b8a6"/></svg>
      555.014.2270
    </p>
    <p class="contact__web">purenestcarpetcare.com</p>
  </div>

  <section class="green-panel">
    <p class="green-claim">We are<span class="green-claim__hand">100% GREEN</span></p>
    <svg class="green-claim__underline" width="180" height="12" viewBox="0 0 180 12" aria-hidden="true"><path d="M2 9 Q90 2 178 4" stroke="#ffffff" stroke-width="3" fill="none" stroke-linecap="round"/></svg>

    <ul class="benefits">
      <li><svg width="26" height="20" viewBox="0 0 26 20" aria-hidden="true"><path d="M2 11 L9 17 L24 2" stroke="#ffffff" stroke-width="3" fill="none" stroke-linecap="round"/></svg>No Harsh Chemicals</li>
      <li><svg width="26" height="20" viewBox="0 0 26 20" aria-hidden="true"><path d="M2 11 L9 17 L24 2" stroke="#ffffff" stroke-width="3" fill="none" stroke-linecap="round"/></svg>No Sticky Residue</li>
      <li><svg width="26" height="20" viewBox="0 0 26 20" aria-hidden="true"><path d="M2 11 L9 17 L24 2" stroke="#ffffff" stroke-width="3" fill="none" stroke-linecap="round"/></svg>Safer People, pet, and Environment</li>
      <li><svg width="26" height="20" viewBox="0 0 26 20" aria-hidden="true"><path d="M2 11 L9 17 L24 2" stroke="#ffffff" stroke-width="3" fill="none" stroke-linecap="round"/></svg>Improve air quality</li>
      <li><svg width="26" height="20" viewBox="0 0 26 20" aria-hidden="true"><path d="M2 11 L9 17 L24 2" stroke="#ffffff" stroke-width="3" fill="none" stroke-linecap="round"/></svg>Dries in minutes not hours</li>
      <li><svg width="26" height="20" viewBox="0 0 26 20" aria-hidden="true"><path d="M2 11 L9 17 L24 2" stroke="#ffffff" stroke-width="3" fill="none" stroke-linecap="round"/></svg>No more wet carpet</li>
    </ul>

    <svg class="guarantee" width="260" height="170" viewBox="0 0 260 170" aria-label="100% Guaranteed">
      <polygon fill="#ffffff" points="
        130,4 138,48 155,8 154,52 178,18 166,58 198,34 176,66 214,54 183,76 226,78 184,88 222,102 180,100 210,124 172,110 190,142 162,116 168,158 150,120 140,166 134,122 118,164 122,120 96,156 110,114 76,140 100,106 60,120 92,96 46,98 90,86 48,74 92,74 58,50 98,64 78,30 108,56 102,14 118,52"/>
      <text x="130" y="92" text-anchor="middle" transform="rotate(16 130 88)" font-family="Lato, sans-serif" font-weight="700" font-size="22" fill="#2b8f82">100% GUARANTEED</text>
    </svg>
  </section>
</main>
</body>
</html>
```